Label design for an exciting new Vodka brand

We need a label design for a dynamic new Vodka brand called 'Pale lantern drift Vodka'. It is a crisp and versatile liquid with a clean and smooth finish. It should appeal to 21-39 year olds, with a slight female skew. Colours, fonts and styles should be modern and relatively neutral - take inspiration from the brand pictures attached.

Target Market(s)

21-39 year olds, both male and female, but with a slight female skew

```html
<!DOCTYPE html>
<html lang="en">
<head>
<meta charset="utf-8">
<title>Pale lantern drift Vodka — Label</title>
<link rel="stylesheet" href="https://fonts.googleapis.com/css2?family=Questrial&display=swap">
<style>
  :root {
    --page: #ffffff;
    --label-sky: #92a8f0;
    --label-violet: #7d7dd9;
    --name-gold: #ffb800;
    --vodka-white: #ffffff;
  }
  * { margin: 0; padding: 0; box-sizing: border-box; }
  html, body {
    width: 1200px;
    height: 1200px;
    overflow: hidden;
    background: var(--page);
  }
  .canvas {
    position: relative;
    width: 1200px;
    height: 1200px;
  }
  .label {
    position: absolute;
    left: 195px;
    top: 60px;
    width: 810px;
    height: 1080px;
    background: var(--label-sky);
    overflow: hidden;
  }
  .label-disc {
    position: absolute;
    inset: 0;
    width: 810px;
    height: 1080px;
  }
  .brand-name {
    position: absolute;
    left: 120px;
    top: 95px;
    font-family: "Questrial", sans-serif;
    font-weight: 400;
    color: var(--name-gold);
    line-height: 0.92;
    font-size: 150px;
    letter-spacing: -2px;
  }
  .brand-name span { display: block; }
  .brand-name .line-two { padding-left: 10px; }
  .brand-name .line-three { padding-left: 90px; }
  .product-type {
    position: absolute;
    left: 0;
    right: 0;
    top: 690px;
    text-align: center;
    font-family: "Questrial", sans-serif;
    font-size: 110px;
    color: var(--vodka-white);
    letter-spacing: 62px;
    padding-left: 62px;
    line-height: 1;
  }
</style>
</head>
<body>
  <main class="canvas">
    <section class="label" aria-label="Pale lantern drift Vodka bottle label">
      <svg class="label-disc" viewBox="0 0 810 1080" aria-hidden="true">
        <circle cx="405" cy="735" r="354" fill="var(--label-violet)"/>
      </svg>
      <h1 class="brand-name">
        <span class="line-one">Pale</span>
        <span class="line-two">lantern</span>
        <span class="line-three">drift</span>
      </h1>
      <p class="product-type">VODKA</p>
    </section>
  </main>
</body>
</html>
```